Four in One (Flexible infographic for Content Management Industry)

See attachment.
A graphic depicting 4 products, where each can stand on its own and each can be combined with others, but where, if all are taken together, the best result is achieved (the "super product").
Intended use is web. See attached file as an example.
The most basic idea is as the attached diagram shows, where 4 rectangles are arranged in a quadrangle, with a middle rectangle in the center representing the combined 4 products. This concept is fine except it is a bit too obvious as it stands. We are looking for either a variation of this or another concept.
The audience is technical + professional + enterprise - NOT consumers. Hence the design should be conservative in nature.
We are aware of tools like as Canva or Pictogram where such graphics are available, but we are looking for something with a bit more imagination and flexibility.
This graphic should be targeted to web sites and be delivered with vector-based (SVG) graphics.

```html
<!DOCTYPE html>
<html lang="en">
<head>
<meta charset="utf-8">
<title>Four in One – Super Product</title>
<link href="https://fonts.googleapis.com/css2?family=Arimo:wght@400;700&family=Open+Sans:wght@400;800&display=swap" rel="stylesheet">
<style>
  :root {
    --bg: #ffffff;
    --orange-a: #fcc015;
    --orange-b: #f0862a;
    --teal-a: #0bb49a;
    --teal-b: #00928f;
    --blue-a: #00a9e6;
    --blue-b: #0177bc;
    --navy-a: #0a5da0;
    --navy-b: #0a3a62;
    --title-1: #1771b8;
    --title-2: #f18f1e;
    --title-3: #2e3191;
    --title-4: #27b06f;
    --body: #9a9a9a;
    --core-text: #4a4646;
    --core-line: #dfe3e8;
  }
  html, body { margin: 0; padding: 0; overflow: hidden; background: var(--bg); }
  .canvas { width: 1200px; height: 854px; position: relative; }
  .canvas svg { display: block; }
  .block-title { font-family: "Arimo", Arial, sans-serif; font-weight: 700; font-size: 24.5px; text-anchor: middle; }
  .block-body { font-family: "Arimo", Arial, sans-serif; font-size: 15.7px; fill: var(--body); text-anchor: middle; }
  .step-number { font-family: "Open Sans", sans-serif; font-weight: 800; fill: #fff; text-anchor: middle; }
  .core-kicker { font-family: "Open Sans", sans-serif; font-size: 16px; fill: var(--core-text); text-anchor: middle; }
  .core-name { font-family: "Open Sans", sans-serif; font-weight: 800; font-size: 26px; fill: var(--core-text); text-anchor: middle; }
</style>
</head>
<body>
<div class="canvas">
<svg width="1200" height="854" viewBox="0 0 1200 854" xmlns="http://www.w3.org/2000/svg">
  <defs>
    <linearGradient id="grad-orange" x1="0" y1="0" x2="1" y2="1">
      <stop offset="0" stop-color="var(--orange-a)"/><stop offset="1" stop-color="var(--orange-b)"/>
    </linearGradient>
    <linearGradient id="grad-teal" x1="0" y1="0" x2="1" y2="1">
      <stop offset="0" stop-color="var(--teal-a)"/><stop offset="1" stop-color="var(--teal-b)"/>
    </linearGradient>
    <linearGradient id="grad-blue" x1="0" y1="0" x2="1" y2="1">
      <stop offset="0" stop-color="var(--blue-a)"/><stop offset="1" stop-color="var(--blue-b)"/>
    </linearGradient>
    <linearGradient id="grad-navy" x1="0" y1="0" x2="1" y2="1">
      <stop offset="0" stop-color="var(--navy-a)"/><stop offset="1" stop-color="var(--navy-b)"/>
    </linearGradient>
    <filter id="soft-shadow" x="-30%" y="-30%" width="160%" height="160%">
      <feDropShadow dx="5" dy="7" stdDeviation="7" flood-color="#000" flood-opacity="0.14"/>
    </filter>
  </defs>

  <!-- Product circles -->
  <g class="product-circles" filter="url(#soft-shadow)">
    <circle class="circle-01" cx="584" cy="274" r="84" fill="url(#grad-orange)"/>
    <circle class="circle-02" cx="703" cy="392" r="84" fill="url(#grad-teal)"/>
    <circle class="circle-04" cx="465" cy="392" r="84" fill="url(#grad-blue)"/>
    <circle class="circle-03" cx="584" cy="511" r="84" fill="url(#grad-navy)"/>
  </g>

  <!-- Combined core -->
  <g class="core" filter="url(#soft-shadow)">
    <rect class="core-plate" x="494" y="302" width="180" height="180" rx="22"
          transform="rotate(45 584 392)" fill="#fff"/>
  </g>
  <rect class="core-outline" x="516" y="324" width="136" height="136" rx="14"
        transform="rotate(45 584 392)" fill="none" stroke="var(--core-line)" stroke-width="2"/>
  <g class="core-dots">
    <circle cx="584" cy="312" r="5" fill="var(--orange-b)"/>
    <circle cx="664" cy="392" r="5" fill="var(--teal-a)"/>
    <circle cx="584" cy="472" r="5" fill="var(--navy-a)"/>
    <circle cx="504" cy="392" r="5" fill="var(--blue-a)"/>
  </g>

  <!-- Step numbers -->
  <text class="step-number" x="583" y="234" font-size="25">01</text>
  <text class="step-number" x="759" y="402" font-size="29">02</text>
  <text class="step-number" x="584" y="574" font-size="25">03</text>
  <text class="step-number" x="408" y="402" font-size="29">04</text>

  <!-- Core label -->
  <text class="core-kicker" x="584" y="377">SUPER</text>
  <text class="core-name" x="584" y="407">PRODUCT</text>

  <!-- Text blocks -->
  <g class="text-block block-tl">
    <text class="block-title" x="346" y="165" fill="var(--title-1)">TITLE GOES HERE</text>
    <text class="block-body">
      <tspan x="342" y="197">Lorem ipsum dolor sit amet,</tspan>
      <tspan x="342" y="215.5">consectetuer dolore  adipiscing elit,</tspan>
      <tspan x="342" y="234">sed diam nonummy nibh euismod</tspan>
      <tspan x="342" y="252.5">tincidunt ut laoreet dolore magna</tspan>
      <tspan x="342" y="271">aliquam.</tspan>
    </text>
  </g>
  <g class="text-block block-tr">
    <text class="block-title" x="827" y="165" fill="var(--title-2)">TITLE GOES HERE</text>
    <text class="block-body">
      <tspan x="823" y="197">Lorem ipsum dolor sit amet,</tspan>
      <tspan x="823" y="215.5">consectetuer dolore  adipiscing elit,</tspan>
      <tspan x="823" y="234">sed diam nonummy nibh euismod</tspan>
      <tspan x="823" y="252.5">tincidunt ut laoreet dolore magna</tspan>
      <tspan x="823" y="271">aliquam.</tspan>
    </text>
  </g>
  <g class="text-block block-bl">
    <text class="block-title" x="346" y="527" fill="var(--title-3)">TITLE GOES HERE</text>
    <text class="block-body">
      <tspan x="342" y="560">Lorem ipsum dolor sit amet,</tspan>
      <tspan x="342" y="578.5">consectetuer dolore  adipiscing elit,</tspan>
      <tspan x="342" y="597">sed diam nonummy nibh euismod</tspan>
      <tspan x="342" y="615.5">tincidunt ut laoreet dolore magna</tspan>
      <tspan x="342" y="634">aliquam.</tspan>
    </text>
  </g>
  <g class="text-block block-br">
    <text class="block-title" x="827" y="527" fill="var(--title-4)">TITLE GOES HERE</text>
    <text class="block-body">
      <tspan x="823" y="560">Lorem ipsum dolor sit amet,</tspan>
      <tspan x="823" y="578.5">consectetuer dolore  adipiscing elit,</tspan>
      <tspan x="823" y="597">sed diam nonummy nibh euismod</tspan>
      <tspan x="823" y="615.5">tincidunt ut laoreet dolore magna</tspan>
      <tspan x="823" y="634">aliquam.</tspan>
    </text>
  </g>
</svg>
</div>
</body>
</html>
```